Construction material supplies company business card ****

1. Full company name “K T Masonry Works Ltd”
I am after a Business card design for the company as a whole. We are better known in Solomon Islands as “K T Masonry” for short.

We are a building materials supplier of
Ready Mixed Concrete, Bricks and Blocks,
Quarry products- gravel, aggregates, sand etc.
Cement distributor/retailer of reputable brands.
Other prefab concrete products. Culverts, wave breakers, concrete retaining blocks etc.

2. Competitive Advantage over Competition: Quality, efficient, professional, dependable, reliable

3. We want people to feel trust worthy, high quality, strong when they see our brand

5. No preference to color. Maybe more sturdy and corporate. Not fancy.

Industry/Entity Type

CONSTRUCTION SUPPLY

Contact Information for Business Card

Name, Position, office phone mob phone, email

Requirements
Must have
• the company logo
Nice to have
• would like to see a mixture of designs, of with logo only and also with simple graphic designs to bring out the company whilst still have the strong sturdy professional feeling

```html
<!DOCTYPE html>
<html lang="en">
<head>
<meta charset="utf-8">
<title>K T Masonry — Business Card</title>
<link rel="stylesheet" href="https://fonts.googleapis.com/css2?family=Montserrat:wght@400;700;800&display=swap">
<style>
  :root {
    --navy: #163f66;
    --navy-deep: #0f3052;
    --navy-light: #1f5a8f;
    --white: #ffffff;
    --shadow-grey: #a9adb3;
    --backdrop: #1b1b1d;
    --card-w: 540px;
    --card-h: 309px;
  }
  * { box-sizing: border-box; margin: 0; padding: 0; }
  html, body { width: 1200px; height: 900px; overflow: hidden; }
  body {
    background: var(--backdrop);
    font-family: "Montserrat", Arial, sans-serif;
  }
  .sheet {
    width: 1200px; height: 900px;
    display: flex; align-items: center; justify-content: center;
    gap: 40px;
  }
  .card {
    position: relative;
    width: var(--card-w); height: var(--card-h);
    border-radius: 22px;
    overflow: hidden;
    background: var(--navy);
  }
  .card-art { position: absolute; inset: 0; }

  .wordmark {
    font-weight: 800;
    letter-spacing: 0.04em;
    text-transform: uppercase;
    display: flex; align-items: center; gap: 9px;
    white-space: nowrap;
  }
  .wordmark-square { width: 18px; height: 18px; flex: none; }

  .card-front .wordmark {
    position: absolute; right: 26px; top: 98px;
    color: var(--navy); font-size: 26px;
  }
  .card-front .wordmark-square { background: var(--navy); }

  .contact {
    position: absolute; left: 30px; top: 150px;
    color: var(--white);
  }
  .contact-name { font-weight: 700; font-size: 15px; letter-spacing: 0.04em; text-transform: uppercase; }
  .contact-role { font-size: 11px; margin: 2px 0 9px; }
  .contact-line { display: flex; align-items: center; gap: 6px; font-size: 11px; line-height: 1.6; }
  .contact-line svg { width: 10px; height: 10px; flex: none; }

  .card-back .pattern-area {
    position: absolute; inset: 0;
    background: linear-gradient(135deg, var(--navy-deep) 0%, var(--navy) 55%, var(--navy-light) 100%);
  }
  .card-back .wordmark {
    position: absolute; right: 34px; bottom: 58px;
    color: var(--white); font-size: 28px;
  }
  .card-back .wordmark-square { background: var(--white); }
</style>
</head>
<body>
<main class="sheet">

  <section class="card card-front" aria-label="Card front">
    <svg class="card-art" viewBox="0 0 540 309" preserveAspectRatio="none" aria-hidden="true">
      <path d="M150,0 C190,170 370,250 540,262 L540,0 Z" fill="var(--white)"/>
      <path d="M160,30 C205,185 380,248 540,258 L540,262 C370,250 190,170 150,0 Z" fill="var(--shadow-grey)"/>
      <path d="M150,10 C185,190 360,268 540,280" fill="none" stroke="var(--white)" stroke-width="4"/>
    </svg>

    <div class="wordmark"><span class="wordmark-square"></span>K T Masonry</div>

    <div class="contact">
      <p class="contact-name">Daniel Harlow</p>
      <p class="contact-role">President</p>
      <p class="contact-line">
        <svg viewBox="0 0 10 10"><path d="M2 0.5 L4 2.5 L3 3.8 C3.8 5.4 4.6 6.2 6.2 7 L7.5 6 L9.5 8 L8 9.5 C4 9 1 6 0.5 2 Z" fill="currentColor"/></svg>
        677-24-3190
      </p>
      <p class="contact-line">
        <svg viewBox="0 0 10 10"><rect x="0.5" y="2" width="9" height="6" fill="none" stroke="currentColor"/><path d="M0.5 2 L5 5.5 L9.5 2" fill="none" stroke="currentColor"/></svg>
        info@ktmasonry.com
      </p>
      <p class="contact-line">
        <svg viewBox="0 0 10 10"><circle cx="5" cy="5" r="4.4" fill="none" stroke="currentColor"/><path d="M0.6 5 H9.4 M5 0.6 C2.5 3 2.5 7 5 9.4 M5 0.6 C7.5 3 7.5 7 5 9.4" fill="none" stroke="currentColor" stroke-width="0.8"/></svg>
        www.ktmasonry.com
      </p>
    </div>
  </section>

  <section class="card card-back" aria-label="Card back">
    <div class="pattern-area" role="img" aria-label="Repeating embossed brand-mark pattern in blue tones"></div>
    <div class="wordmark"><span class="wordmark-square"></span>K T Masonry</div>
  </section>

</main>
</body>
</html>
```